Small Business Directory Site Requires a Professional Responsive Web Design

Small Business Directory and Coupon Site - we require a complete website design for a brand new responsive & mobile friendly website. We already have a coder who will professional code our website in Magento.

All PSD pages need to be professionally designed then uploaded into a sharedrive (i.e. like filecrate). Additionally, as I cannot pre-empt everything, please note that we may require a little more assistance once the files have been transferred (for example, in www.brightlane-listings.example if you hover your mouse on the search box you will see a pop up box. We want one of these too and I think that means there may be extra design work here)

We have some draft page sketches have been created (there are some minor changes we want to the sketches provided though); however, we require an excellent designer to add the creative touches to it to make it look professionally created. All artwork/font must be legal.

-------------------------
We like the look of the www.brightlane-listings.example and www. marlowfolio.example

For the headers, please consider a font similar to RNS camellia. We likes this style, but it is too thin for the headers...so we need a variation like this one. For the copy/general text font, something basic that marries well with the headers.

---------------------

Please be sure to also read the brief we wrote for the coder as this will help with better understanding our design requirements.

In total I believe we have about 50 pages. This includes all the little pages and most of the pop up boxes (but not the little help key boxes). For example, pages include...

1. Login (this is where customers log in and can edit, manage their profiles. This means that there are backend membership pages)
2. Mini Services (same look and feel as the business coupons)
3. Resource Centre
4. Join (this is where customers learn about the packages available to submit a directory listing, if they ‘buy’ a package (i.e. free, $25 or $150 package) then they can create their own directory listing)
5. Search the directory (customer can view all the categories and also search the directory)
6. Create a directory listing (this is where customers learn about the packages available to submit a directory listing, if they ‘buy’ a package (i.e. free, $25 or $150 package) then they can create their own directory listing)
7. Quote finder (also know as Get a Quote)
8. Coupons (customer go to the business coupon page and can view all current coupons/submit a coupon)
9. Submit a coupon (form)
10.Advertise with us (form)
11. Join the forum
12.Submit an article or video (form)
13. Affiliates (listing of affiliates we currently have)
14. Become an affiliate (form)
15. Case studies (customer can view the case studies we have in the resource centre)
16. Help Guides (customer can view the help guides we have in the resource centre)
17. About Us
18 .Contact Us (form)
19. Terms & Condition
20. Privacy Policy
21. Supporting City Councils
22. Site Map
23. Forgot password / login details
24. Homepage
25. If we hover over a few areas (i.e. search box, location field) it pops up with more information.
etc etc etc. . . there are more pages.

Please see our filecrate link for the draft mock up pages that I have created so far.

https://www.cloudtrunk.example/sh/qk72pmw4rtz8nd/KLMvbTq2fWndxPzs8Yh4ecRQu

We are in a rush! We'd like to get the majority of the artwork completed by the end of the month. Minor fixes/tweaks can occur thereafter.

Target Market(s)

Small Businesses (employees 0 - 50) located throughout Australia

Industry/Entity Type

Business

Font styles to use
Sans Serif

Requirements
Must have
• Professional. Artwork must be legal (cannot be cut and paste or taken off other websites, must be legally purchased and used).Must look contemporary, fresh, modern.

Absolutely must be a responsive site!
Nice to have
• original work, original photos, original art.

like modern, fresh photos that demonstrate innovation, growth, small business, Australian scenery, stability, goals/passion.
Should not have
• cut and paste graphics, illegal graphics, not purchased graphics.

```html
<!DOCTYPE html>
<html lang="en">
<head>
<meta charset="utf-8">
<title>SB Harbourline – Small Business Directory</title>
<link rel="stylesheet" href="https://fonts.googleapis.com/css2?family=Ubuntu:wght@300;400;500;700&family=Open+Sans:wght@400;600&display=swap">
<style>
:root{
  --orange:#f47b20;
  --orange-dark:#e0680f;
  --ink:#1f1f1f;
  --black:#0d0d0d;
  --charcoal:#1a1a1a;
  --grey-text:#6b6b6b;
  --light-line:#d9d9d9;
  --white:#ffffff;
  --footer-text:#cfcfcf;
}
*{box-sizing:border-box;margin:0;padding:0}
html,body{width:1200px;height:2773px;overflow:hidden}
body{position:relative;background:var(--white);font-family:"Open Sans",Arial,sans-serif;color:var(--ink)}
.abs{position:absolute}
.heading{font-family:"Ubuntu",Arial,sans-serif}

/* header */
.site-header{left:0;top:0;width:1200px;height:100px;background:var(--black);border-top:4px solid var(--orange)}
.brand{left:111px;top:36px;display:flex;align-items:center;gap:12px;color:var(--white);font-family:"Ubuntu",sans-serif;font-size:23px;font-weight:500;letter-spacing:.5px}
.brand-mark{width:28px;height:28px;background:var(--orange)}
.like-box{left:890px;top:8px;width:76px;height:22px;background:#3b5998;border-radius:2px}
.account-tab{left:975px;top:0;width:112px;height:33px;background:var(--orange);color:var(--white);font-family:"Ubuntu",sans-serif;font-size:14px;font-weight:500;display:flex;align-items:center;justify-content:center;gap:8px}
.main-nav{left:518px;top:52px;display:flex;align-items:center;gap:0;font-family:"Ubuntu",sans-serif;font-size:14px;color:var(--white)}
.main-nav span{padding:0 13px;line-height:29px}
.main-nav .is-active{background:var(--orange);border-radius:2px;padding:0 18px;margin-right:10px}

/* hero */
.hero{left:0;top:100px;width:1200px;height:664px;background:linear-gradient(180deg,#6f9fc9 0%,#b9cfd8 30%,#e7c98a 50%,#c89a3a 70%,#8d6a1f 100%)}
.hero-shadow{left:40px;top:764px;width:1120px;height:22px;background:radial-gradient(ellipse at top,rgba(0,0,0,.25),rgba(0,0,0,0) 70%)}
.hero-title{left:107px;top:286px;font-family:"Ubuntu",sans-serif;font-weight:400;font-size:40px;line-height:46px;color:var(--ink);text-transform:uppercase}
.hero-title em{font-style:normal;color:var(--orange);font-weight:500}
.search-panel{left:109px;top:410px;width:549px;height:63px;background:var(--black)}
.search-input{top:17px;height:37px;background:var(--white);font-size:13px;color:#555;padding-left:12px;display:flex;align-items:center}
.search-go{left:475px;top:17px;width:61px;height:37px;background:var(--orange);color:var(--white);font-family:"Ubuntu",sans-serif;font-size:19px;display:flex;align-items:center;justify-content:center}
.category-bar{left:109px;top:473px;width:549px;height:52px;background:var(--orange);display:flex;align-items:center;justify-content:space-around;padding:0 10px;color:var(--white);font-family:"Ubuntu",sans-serif;font-size:13px;font-weight:500;text-transform:uppercase}
.category-bar span{display:flex;align-items:center;gap:8px}

/* section titles */
.section-title{width:1200px;text-align:center;font-family:"Ubuntu",sans-serif;font-size:40px;font-weight:400}
.section-title em{font-style:normal;color:var(--orange)}
.rule{height:1px;background:var(--light-line)}

/* offers */
.intro{left:230px;top:872px;width:740px;text-align:center;font-size:13px;line-height:19px;color:var(--grey-text)}
.offer-card{top:963px;width:198px;text-align:center}
.offer-photo{width:198px;height:119px}
.offer-name{margin-top:14px;font-size:13px;color:#333;text-transform:uppercase}
.offer-text{margin-top:4px;font-size:12px;line-height:17px;color:var(--grey-text)}
.btn{background:var(--orange);color:var(--white);font-family:"Ubuntu",sans-serif;display:flex;align-items:center;justify-content:center;border-radius:2px}

/* dark feature */
.feature{left:0;top:1289px;width:1200px;height:566px;background:linear-gradient(135deg,#262626,#121212)}
.tablet{left:111px;top:1448px;width:477px;height:407px;background:var(--white);border-radius:22px 22px 0 0}
.tablet-screen{left:48px;top:55px;width:381px;height:352px;background:linear-gradient(180deg,#3d4a2c 0%,#3d4a2c 45%,#f2f2f2 45%,#f2f2f2 82%,#2a2a2a 82%)}
.feature-copy{left:638px;top:1505px;color:var(--white)}
.feature-copy h3{font-family:"Ubuntu",sans-serif;font-weight:300;font-size:40px;line-height:50px}
.feature-copy h3 strong{color:var(--orange);font-weight:700}
.feature-copy p{margin-top:14px;font-size:20px;line-height:28px;font-family:"Ubuntu",sans-serif;font-weight:300}

/* support */
.col-title{font-family:"Ubuntu",sans-serif;font-size:21px;text-transform:uppercase;color:#222}
.tab{top:2052px;height:40px;font-family:"Ubuntu",sans-serif;font-size:16px;color:var(--white);display:flex;align-items:center;justify-content:center}
.event-row{left:152px;width:431px;height:46px;border-top:1px solid var(--light-line);display:flex;align-items:center;gap:14px;font-size:13px;color:#333}
.date-tag{background:var(--orange);color:var(--white);font-size:12px;padding:3px 8px;font-weight:600}

/* footer */
.site-footer{left:0;top:2443px;width:1200px;height:330px;background:var(--charcoal)}
.foot-col{top:40px;color:var(--footer-text)}
.foot-col h4{font-family:"Ubuntu",sans-serif;font-weight:400;font-size:16px;color:var(--white);text-transform:uppercase;margin-bottom:18px}
.foot-col li{list-style:none;font-size:12px;line-height:27px}
.subscribe-field{width:255px;height:35px;background:var(--white);display:flex;align-items:center;justify-content:space-between;padding-left:8px;border-radius:2px}
.social{display:flex;gap:9px;margin-top:14px}
.social i{width:26px;height:26px;border-radius:50%;display:block}
.copyright{left:0;top:2733px;width:1200px;text-align:center;font-size:12px;color:var(--footer-text)}
</style>
</head>
<body>

<header class="abs site-header">
  <div class="abs brand"><span class="brand-mark"></span>SB Harbourline</div>
  <div class="abs like-box" role="img" aria-label="Social like button"></div>
  <div class="abs account-tab"><span>Join</span><span>|</span><span>Login</span></div>
  <nav class="abs main-nav">
    <span class="is-active">Join</span><span>Coupons</span><span>Mini Service</span><span>Get a Quote</span><span>Advertise</span><span>Resource Centre</span>
  </nav>
</header>

<section class="abs hero" role="img" aria-label="Golden grassland with a large tree under a clear morning sky"></section>
<div class="abs hero-shadow"></div>
<h1 class="abs hero-title">It's a brand <em>new day</em><br>Do <em>more</em> of what you love</h1>
<div class="abs search-panel">
  <div class="abs search-input" style="left:17px;width:290px">What are you looking for?</div>
  <div class="abs search-input" style="left:316px;width:148px;justify-content:space-between;padding-right:10px">Near where?<span style="font-size:9px">▼</span></div>
  <div class="abs search-go">GO</div>
</div>
<div class="abs category-bar">
  <span><svg width="14" height="14" viewBox="0 0 14 14"><rect x="1" y="5" width="12" height="8" fill="#fff"/><rect x="4" y="2" width="6" height="3" fill="none" stroke="#fff" stroke-width="1.5"/></svg>Banking</span>
  <span><svg width="16" height="13" viewBox="0 0 16 13"><rect x="0" y="3" width="16" height="10" rx="1" fill="#fff"/><rect x="5" y="0" width="6" height="3" fill="#fff"/><circle cx="8" cy="8" r="3" fill="#f47b20"/></svg>Photography</span>
  <span><svg width="16" height="11" viewBox="0 0 16 11"><rect x="0" y="0" width="11" height="11" rx="1" fill="#fff"/><path d="M11 5.5 16 2v7z" fill="#fff"/></svg>Video &amp; Print</span>
  <span><svg width="15" height="15" viewBox="0 0 15 15"><circle cx="7.5" cy="7.5" r="5" fill="none" stroke="#fff" stroke-width="3" stroke-dasharray="3 2"/><circle cx="7.5" cy="7.5" r="2" fill="#fff"/></svg>Design</span>
</div>

<!-- Featured offers -->
<div class="abs rule" style="left:0;top:846px;width:375px"></div>
<div class="abs rule" style="left:825px;top:846px;width:375px"></div>
<h2 class="abs section-title" style="left:0;top:815px">Featured Business <em>Offers</em></h2>
<p class="abs intro">Lorem ipsum dolor sit amet consectetur adipiscing elit sed do eiusmod tempor incididunt labore et dolore magna aliqua ut enim ad minim veniam, quis nostrud exercitation ullamco laboris nisi ut aliquip.</p>

<svg class="abs" style="left:84px;top:1022px" width="16" height="34" viewBox="0 0 16 34"><path d="M13 2 3 17l10 15" fill="none" stroke="#555" stroke-width="2"/></svg>
<svg class="abs" style="left:1100px;top:1022px" width="16" height="34" viewBox="0 0 16 34"><path d="M3 2l10 15L3 32" fill="none" stroke="#555" stroke-width="2"/></svg>

<div class="abs offer-card" style="left:142px"><div class="offer-photo" role="img" aria-label="Customers being served at a bank counter" style="background:linear-gradient(135deg,#c9a27a,#7a5a3e)"></div><p class="offer-name">Join Mobile Perks Club</p><p class="offer-text">Text your name and number to<br>123123 to receive updates</p></div>
<div class="abs offer-card" style="left:381px"><div class="offer-photo" role="img" aria-label="Businessman facing a chalkboard of sketched ideas" style="background:linear-gradient(135deg,#6d6d6d,#2f2f2f)"></div><p class="offer-name">Join Mobile Perks Club</p><p class="offer-text">Text your name and number to<br>123123 to receive updates</p></div>
<div class="abs offer-card" style="left:619px"><div class="offer-photo" role="img" aria-label="Business team meeting in a bright office" style="background:linear-gradient(135deg,#e3e6ea,#6b7c8f)"></div><p class="offer-name">Join Mobile Perks Club</p><p class="offer-text">Text your name and number to<br>123123 to receive updates</p></div>
<div class="abs offer-card" style="left:858px"><div class="offer-photo" role="img" aria-label="City street at night with warm lights" style="background:linear-gradient(135deg,#3a2a40,#b0602a)"></div><p class="offer-name">Join Mobile Perks Club</p><p class="offer-text">Text your name and number to<br>123123 to receive updates</p></div>

<div class="abs rule" style="left:185px;top:1215px;width:213px;background:#bbb"></div>
<div class="abs" style="left:418px;top:1205px;font-size:14px;color:#555">Signup for Daily Deals</div>
<div class="abs btn" style="left:599px;top:1194px;width:179px;height:41px;font-size:16px">Submit An Offer</div>
<div class="abs rule" style="left:795px;top:1215px;width:274px;background:#bbb"></div>

<!-- Feature your business -->
<section class="abs feature" role="img" aria-label="Dim office interior behind the feature panel"></section>
<div class="abs rule" style="left:0;top:1371px;width:370px;background:#777"></div>
<div class="abs rule" style="left:830px;top:1371px;width:370px;background:#777"></div>
<h2 class="abs section-title" style="left:0;top:1342px;color:#fff">Feature Your <em>Business</em></h2>
<div class="abs tablet">
  <svg class="abs" style="left:234px;top:26px" width="8" height="8"><circle cx="4" cy="4" r="3" fill="#bbb"/></svg>
  <div class="abs tablet-screen" role="img" aria-label="Preview of the directory homepage on a tablet screen"></div>
</div>
<div class="abs feature-copy">
  <h3>Drive more sales to your<br>business.It's <strong>RISK FREE.</strong></h3>
  <p>We don't get paid unless you get paid.<br>Speak to us to create a business coupon.</p>
</div>
<div class="abs btn" style="left:640px;top:1703px;width:126px;height:37px;font-size:21px;font-weight:500">Submit</div>

<!-- Get real support -->
<div class="abs rule" style="left:30px;top:1939px;width:380px"></div>
<div class="abs rule" style="left:790px;top:1939px;width:380px"></div>
<svg class="abs" style="left:415px;top:1933px" width="12" height="12"><circle cx="6" cy="6" r="5" fill="#d0d0d0"/></svg>
<svg class="abs" style="left:773px;top:1933px" width="12" height="12"><circle cx="6" cy="6" r="5" fill="#d0d0d0"/></svg>
<h2 class="abs section-title" style="left:0;top:1912px">Get <em>Real Support</em></h2>

<h3 class="abs col-title" style="left:156px;top:2013px">Business Spotlight</h3>
<div class="abs tab" style="left:152px;width:221px;background:var(--orange)">Daily Events</div>
<svg class="abs" style="left:256px;top:2091px" width="14" height="8"><path d="M0 0h14L7 7z" fill="#f47b20"/></svg>
<div class="abs tab" style="left:379px;width:198px;background:#2c2c2c">Events Calender</div>
<div class="abs" role="img" aria-label="Conference room with a seated audience" style="left:152px;top:2119px;width:192px;height:96px;background:linear-gradient(135deg,#8c8a80,#3e4a3a)"></div>
<div class="abs date-tag" style="left:284px;top:2191px">21 JUNE</div>
<p class="abs" style="left:359px;top:2118px;width:222px;font-size:13px;line-height:19px;color:#333">What is leadership? How does poor leadership affect business start of blog post or resource post to get them interesting in reading....</p>
<div class="abs event-row" style="top:2234px"><span class="date-tag">22 JUNE</span>Lorem Ipsum dolor sit amet and typesetting industry</div>
<div class="abs event-row" style="top:2280px;border-bottom:1px solid var(--light-line)"><span class="date-tag">26 JUNE</span>Lorem Ipsum dolor sit amet and typesetting industry</div>
<div class="abs btn" style="left:152px;top:2339px;width:116px;height:37px;font-size:13px;font-weight:500">Read More</div>

<h3 class="abs col-title" style="left:629px;top:2013px">Why SBHL?</h3>
<div class="abs" role="img" aria-label="Business partners shaking hands in an office" style="left:631px;top:2047px;width:425px;height:198px;background:linear-gradient(135deg,#e8eef4,#5a6f8c)"></div>
<h4 class="abs heading" style="left:631px;top:2258px;font-size:18px;font-weight:400;color:var(--orange);text-transform:uppercase">Affiliate ABC Brand</h4>
<p class="abs" style="left:631px;top:2287px;width:440px;font-size:13px;line-height:19px;color:#333">We are collaborating with networking groups around the country to bring our members more support and greater choice</p>
<div class="abs btn" style="left:631px;top:2339px;width:116px;height:37px;font-size:13px;font-weight:500">Read More</div>

<!-- Footer -->
<footer class="abs site-footer">
  <div class="abs foot-col" style="left:111px">
    <h4>Site Directory</h4>
    <ul><li>Search the Directory</li><li>Create a Directory Listing</li><li>Quote Finder</li><li>Coupons</li><li>Submite A Coupons</li><li>Advertise with US</li></ul>
  </div>
  <div class="abs foot-col" style="left:359px">
    <h4>Resources</h4>
    <ul><li>Joine the forum</li><li>submit an Article or video</li><li>Affiliates</li><li>Become an Affiliate</li><li>Case Studies</li><li>Help Guides</li></ul>
  </div>
  <div class="abs foot-col" style="left:601px">
    <h4>About</h4>
    <ul><li>About Us</li><li>Contact Us</li><li>Terms and Conditions</li><li>Privacy Policy</li><li>Supporting&nbsp; City Councils</li><li>Site map</li></ul>
  </div>
  <div class="abs foot-col" style="left:834px">
    <h4>Subscribe Us</h4>
    <p style="font-size:12px;line-height:21px;width:270px">Receive our latest offers, stories &amp; event news, direct to your inbox</p>
    <div class="subscribe-field" style="margin-top:12px">
      <span style="font-size:11px;color:#aaa">Enter email address</span>
      <span class="btn" style="width:64px;height:27px;font-size:11px;font-weight:700;margin-right:4px">SIGN UP</span>
    </div>
    <div class="social">
      <i style="background:#3b5998"></i><i style="background:#d9342b"></i><i style="background:#dc4a38"></i><i style="background:#2aa9e0"></i>
    </div>
  </div>
  <div class="abs rule" style="left:111px;top:271px;width:978px;background:#3a3a3a"></div>
</footer>
<p class="abs copyright">© 2014 Harbourline. All Rights Reserved</p>

</body>
</html>
```